Interior Design for Every Day, Nora Whitfield Interior Design, LLC

We are looking for a website for an Interior Design Company targeted at higher income households. We prefer to work with clients that seek to amplify the architectural beauty of their interior space via interior design - while ensuring the space promotes easy living. For example: a kitchen should be lain out in an intuitive manner such that all utensils, cups and plates are easy to find. Living rooms should be arranged to promote conversation and/or watch TV, etc.... We have heavy reliance on the technical aspects of design (computer automated renderings). We like the look and feel of this website: https://www.brenthalvorsen.example/portfolioall

Target Market(s)

Upper HHI ($200,000+) in the Atlanta Metro Market. Customers are likely to be highly educated and from a variety of cultural backgrounds. Ages 35-60

Industry/Entity Type

Architecture

Font styles to use
Sans Serif

Colors

Designer to choose colors to be used in the design.

Requirements
Must have
• Landing Page, Page demonstrating how interior design fits into the architectural design process, About Us Page with contact info, Example Work Page and Tailored Client Page. Minimal work can be done on the About Us and example work pages. The tailored client page just needs a good layout (and easy uploads and download capability)
• Also to include:
• (1) The landing page should include a Design Philosophy Section and maybe a couple examples of our work and/or pictures you provide
• (2) The Design Process page should explain all steps of the architectural Design process and should explain where interior design/decorating fits into the Architectural process (see below attachments).
• (3) The Example work page should include areas for portfolio example uploads (to include 3 dimensional and 2 dimensional renderings, photos and videos).
• (4) Include a Password Protected, Secure Place where each individual client can store and retrieve documents and work product for their project (Should be a separate page). There should be sections (for each client) for:
• (a) there should be a client account creation requirement page that requires: FN, LN, Mobile, email, Work phone, Property address, City, Zip (for 3 properties), Spouse FN, Spouse LN, Child FN, LN (space for 5 children)
• (a) section: Legal & Invoices
• (b) section: Drawings & Renderings
• (c) section: Pin Ups (easy uploads of pictures from sites like snapboardia would be appreciated) - pin ups should be very easy for clients to put examples of what they like
• (5) Ability for admin to use personalized password and username to view, delete and edit client files (we utilize filecrate for document storage currently, and integration with filecrate would be a plus)
• (6) needs to be formatted and optimized for Mobile (iOs and android) viewing as well as Web
• (7) The site should be built with a hosting service contemplated. This service should be affordable (Less than $300 per annum)
• (8) most importantly the site should be minimalist with focus on user friendliness while being fashion forward
• (9) Website Color scheme should be White/Black/BlueGrey
• (10) The site must also include the ability to generate an invoice, based on client registration, electronically submit the invoice to the client via email (or print it), accept payment via coinvoy integration, and generate conformation email of payment to both client and admin (although coinvoy may already do this).
Nice to have
• Ability of example and client pages to be integrated with sites like snapbordia and filecrate. Ability to have some sort of section that self identifies the clients design style(s)...maybe a quiz or at lease a place where they can create a pinboard of images and colors they like (potentially by room)
Should not have
• Must look modern and be extremely quick/user friendly. Our clients are very busy.

```html
<!DOCTYPE html>
<html lang="en">
<head>
<meta charset="utf-8">
<title>Nora Whitfield Interior Design, LLC</title>
<link rel="stylesheet" href="https://fonts.googleapis.com/css2?family=Mulish:wght@300;400;600;700&display=swap">
<style>
:root{
  --ink:#2b2b2b;
  --muted:#8a8a8a;
  --soft:#a9a9a9;
  --blue:#2a8fd6;
  --band:#22a1e4;
  --footer:#7d7d7d;
  --white:#ffffff;
  --sky:#b7bbc0;
  --siding:#e4e5e5;
  --roof:#8f9293;
  --foliage:#8c9a86;
}
*{box-sizing:border-box;margin:0;padding:0}
html,body{width:748px;height:1200px;overflow:hidden;background:var(--white)}
body{position:relative;font-family:"Mulish",sans-serif;color:var(--ink)}
.header-bg{position:absolute;left:0;top:0;width:748px;height:470px;background:linear-gradient(180deg,#f1f1f1 0%,#fafafa 60%,#fff 100%)}
.brand{position:absolute;left:77px;top:14px;line-height:1}
.brand-name{font-size:22px;font-weight:600;letter-spacing:-.3px;line-height:19px;color:var(--ink)}
.brand-sub{margin-top:4px;font-size:8.5px;font-weight:600;line-height:9px;color:var(--ink)}
.main-nav{position:absolute;left:246px;top:44px;display:flex;gap:15px;font-size:10px;letter-spacing:.3px;color:#888}
.main-nav .active{color:var(--ink)}
.hero{position:absolute;left:73px;top:97px;width:603px;height:320px;overflow:hidden}
.hero-art{position:absolute;inset:0;
  background:
    linear-gradient(90deg,rgba(140,154,134,.75) 0%,rgba(140,154,134,0) 10%,rgba(140,154,134,0) 86%,rgba(140,154,134,.7) 100%),
    linear-gradient(180deg,var(--sky) 0%,#d3d5d7 22%,var(--siding) 40%,#eeeeee 62%,#d9dada 74%,var(--roof) 84%,#b5b6b4 92%,#cfcfcd 100%)}
.hero-title{position:absolute;left:0;right:0;top:118px;text-align:center;font-size:26px;font-weight:700;color:var(--blue);letter-spacing:.3px}
.hero-sub{position:absolute;left:0;right:0;top:153px;text-align:center;font-size:17px;font-weight:700;color:#555;letter-spacing:.3px}
.hero-dots{position:absolute;left:245px;top:302px;display:flex;gap:4px}
.hero-dots span{width:21px;height:3px;background:#e4e4e4}
.hero-dots .on{background:var(--blue)}
.about{position:absolute;left:0;right:0;top:463px;text-align:center}
.about h2{font-size:22px;font-weight:700;color:#333}
.about p{width:480px;margin:12px auto 0;font-size:10.5px;line-height:17px;color:var(--muted)}
.btn{display:inline-block;margin-top:20px;width:91px;height:24px;line-height:22px;border:1px solid var(--blue);color:var(--blue);font-size:9.5px;letter-spacing:.3px}
.band{position:absolute;left:0;top:618px}
.philosophy-title{position:absolute;left:0;right:0;top:666px;text-align:center;font-size:19px;font-weight:300;color:var(--white);letter-spacing:.8px}
.philosophy-title::after{content:"";display:block;width:36px;height:1px;margin:4px auto 0;background:var(--white)}
.projects{position:absolute;left:73px;top:715px;display:flex;gap:10px}
.project{width:144px}
.project-art{width:144px;height:130px;border:1px solid #5b6c78}
.art-kitchen{background:linear-gradient(180deg,#f2f2f2 0%,#dcdcdc 50%,#3e3f40 56%,#2f3031 60%,#e9e9e9 64%,#cfcfcf 100%)}
.art-house{background:linear-gradient(180deg,#aeb3b8 0%,#e8e9ea 30%,#d6d7d8 60%,#b9bbbc 80%,#8f9497 100%)}
.art-counter{background:linear-gradient(180deg,#ededed 0%,#d3d4d4 45%,#363738 55%,#2b2c2d 59%,#e6e6e6 63%,#9a9b9b 100%)}
.art-plan{background:radial-gradient(ellipse at 50% 55%,#e6e6e6 0%,#cfcfcf 45%,#7a7c7d 100%)}
.project-title{margin-top:7px;border-top:1px solid var(--white);border-bottom:1px solid var(--white);height:27px;line-height:25px;text-align:center;color:var(--white);font-size:13px;font-weight:300}
.clients-title{position:absolute;left:0;right:0;top:961px;text-align:center;font-size:18px;font-weight:700;color:var(--soft);letter-spacing:.3px}
.clients-title::after{content:"";display:block;width:36px;height:1px;margin:4px auto 0;background:var(--soft)}
.clients{position:absolute;left:90px;width:570px;top:1015px;display:flex;justify-content:space-between;align-items:center;font-size:17px;font-weight:700;color:var(--soft)}
.clients .dot{display:inline-block;width:9px;height:9px;border-radius:50%;background:var(--soft);margin-right:4px}
.footer{position:absolute;left:0;top:1088px}
.footer-nav{position:absolute;left:85px;top:1141px;display:flex;gap:13px;font-size:9px;color:var(--white);letter-spacing:.2px}
.copyright{position:absolute;left:85px;top:1161px;font-size:8px;color:#e6e6e6}
.social{position:absolute;left:560px;top:1134px;display:flex;gap:3px}
.social span{width:26px;height:26px;border:1.3px solid var(--white);border-radius:50%;color:var(--white);font-size:6.5px;font-weight:600;display:flex;align-items:center;justify-content:center}
</style>
</head>
<body>
<div class="header-bg"></div>
<div class="brand">
  <div class="brand-name">NORA<br>WHITFIELD</div>
  <div class="brand-sub">INTERIOR<br>DESIGN<br>LLC</div>
</div>
<nav class="main-nav">
  <span class="active">HOME</span><span>PROCESS</span><span>ABOUT US</span><span>EXAMPLE WORKS</span><span>CLIENT CORNER</span><span>CONTACT US</span>
</nav>

<section class="hero">
  <div class="hero-art" role="img" aria-label="Rendered drawing of a white two-gable house front with trees at the sides"></div>
  <h1 class="hero-title">INTERIOR DESIGN SERVICE</h1>
  <div class="hero-sub">PROIN NULLA ARCU NONUMMY</div>
  <div class="hero-dots"><span></span><span></span><span class="on"></span><span></span></div>
</section>

<section class="about">
  <h2>ABOUT NORA WHITFIELD</h2>
  <p>Vivamus porttitor purus nisi eleifend libero a tempus libero lectus feugiat felis Morbi diam mauris viverra in gravida eu mattis in ante pulvinar metus eget consectetuer augue nisi quis lacus Ut ac mi quis lacus mollis aliquam Curabitur iaculis tempus eros</p>
  <span class="btn">READ MORE</span>
</section>

<svg class="band" width="748" height="326" viewBox="0 0 748 326" role="img" aria-label="Blue band over a faint house rendering">
  <defs>
    <linearGradient id="bandFill" x1="0" y1="0" x2="0" y2="1">
      <stop offset="0" stop-color="#2aa6e6"/>
      <stop offset="1" stop-color="#1f9be0"/>
    </linearGradient>
  </defs>
  <polygon points="0,2 748,42 748,324 0,282" fill="url(#bandFill)"/>
</svg>
<h2 class="philosophy-title">DESIGN PHILOSOPHY</h2>
<div class="projects">
  <div class="project"><div class="project-art art-kitchen" role="img" aria-label="Kitchen rendering with dark counter"></div><div class="project-title">Project Tittle</div></div>
  <div class="project"><div class="project-art art-house" role="img" aria-label="House exterior rendering"></div><div class="project-title">Project Tittle</div></div>
  <div class="project"><div class="project-art art-counter" role="img" aria-label="Kitchen island rendering"></div><div class="project-title">Project Tittle</div></div>
  <div class="project"><div class="project-art art-plan" role="img" aria-label="Kitchen floor plan rendering"></div><div class="project-title">Project Tittle</div></div>
</div>

<h2 class="clients-title">CLIENT CORNER</h2>
<div class="clients">
  <span>SWIFTLY</span><span><i class="dot"></i>Aurento</span><span>LEGATE</span><span>Vemano</span><span>leafy</span><span>TALLOW</span>
</div>

<svg class="footer" width="748" height="112" viewBox="0 0 748 112" aria-hidden="true">
  <polygon points="0,30 748,0 748,112 0,112" fill="#7d7d7d"/>
</svg>
<nav class="footer-nav"><span>HOME</span><span>PROCESS</span><span>ABOUT US</span><span>EXAMPLE WORKS</span><span>CLIENT CORNER</span><span>CONTACT US</span></nav>
<div class="copyright">© 2017 Company Name &nbsp;All right reserved &nbsp;Term of Use</div>
<div class="social"><span>Chirp</span><span>Facet</span><span>Linkr</span><span>Plus</span><span>Snapr</span></div>
</body>
</html>
```